Etikett für Rotweinflasche
Liebe farbkosmos Atelier, wir werden uns bei der endgültigen Etikettengestaltung (finale Größe + Rückseite) noch an Euch melden. Bitte sendet uns euren Kontakt an helga.brandt@morvelli.wine
Zielgruppe
Morvelli Italia ist ein exklusives Boutique-Weingut in Sizilien, das hochqualitative Spitzenweine in kleinen Mengen mit modernster Technologie und stets nachhaltig erzeugt. Wir hinterfragen sowohl in der Agronomie im Weingarten als auch in der Önologie im Weinkeller alle herrschenden Traditionen und trachten danach, stets das beste Endprodukt zu kreieren. Der vulkanische, kalkreiche Boden Siziliens sowie trockene, sonnenreiche und niederschlagsarme Vegetationsperioden sind unsere optimale Basis.
Zielgruppe: Internationale Genussmenschen jeglichen Alters, die sich bewusst auch höherpreisige Weine (um die €30+) gönnen , vor allem kunstaffine young professionals mit Qualitäts-& Nachhaltigkeitsanspruch
Aufgabenstellung
Das Etikett ist für Rotwein-Flaschen (Cabernet Sauvignon / Nero D'Avola / Frappato / Syrah / Cerasuolo / Petit Verdot / sowie einen Bourdeaux-Cuveè aus Cabernet Sauvignon und Petit Verdot) .
Die Flasche ist reinschwarz, sehr hochwertig und schwer.
Flaschenform: Bordeauxflasche siehe technisches Datenblatt
Sleeve über dem Korken: schwarz mit weißer Schrift wie bisher
Zu gestalten ist das Etikett der Vorderseite. Zumindest die jeweilige Rotwein-Sorte ist auch textlich darzustellen (zwecks Scannen mit Trubel-App)
Der Kreativität kann freien Lauf gelassen werden! Unterscheidbarkeit vom Markt ist explizit gewollt.
Unsere aktuellen Etiketten und Markenauftritt siehe: https://morvelli.wine/shop/

```html
<!DOCTYPE html>
<html lang="de">
<head>
<meta charset="utf-8">
<title>Etiketten Rotwein – Nero D'Avola, Cabernet Sauvignon, Frappato</title>
<link rel="stylesheet" href="https://fonts.googleapis.com/css2?family=Bodoni+Moda:opsz,wght@6..96,500;6..96,600&family=Poiret+One&display=swap">
<style>
  :root {
    --page: #ffffff;
    --label-top: #b9b9b9;
    --label-mid: #d2d2d2;
    --label-low: #e4e4e4;
    --ink: #1c1c1c;
    --crimson: #c8003f;
    --wine: #8c0f2f;
    --blush: #f5b0b0;
    --blush-soft: rgba(245, 176, 176, 0.55);
    --dancer-dark: rgba(40, 40, 40, 0.55);
    --dancer-veil: rgba(255, 255, 255, 0.35);
  }
  * { box-sizing: border-box; margin: 0; padding: 0; }
  html, body { width: 882px; height: 1200px; overflow: hidden; background: var(--page); }
  .sheet {
    width: 882px; height: 1200px;
    display: flex; align-items: center; justify-content: center; gap: 27px;
  }
  .label {
    position: relative; width: 252px; height: 398px; overflow: hidden;
    background: linear-gradient(180deg, var(--label-top) 0%, var(--label-mid) 45%, var(--label-low) 100%);
  }
  .label__variety {
    position: absolute; top: 14px; left: 13px; z-index: 5;
    font-family: "Poiret One", sans-serif; font-size: 20px; line-height: 1.25;
    letter-spacing: 3.5px; color: var(--ink);
  }
  .label__variety span { display: block; }
  .label__variety .indent { padding-left: 8px; }
  .label__variety .indent-wide { padding-left: 20px; }
  .label__dancer {
    position: absolute; z-index: 2;
    background: radial-gradient(ellipse at 45% 45%, var(--dancer-dark) 0%, rgba(90,90,90,0.25) 45%, var(--dancer-veil) 70%, transparent 80%);
  }
  .letter {
    position: absolute; font-family: "Bodoni Moda", serif; font-weight: 500; line-height: 1;
  }
  .letter--ghost { color: var(--blush-soft); z-index: 1; font-weight: 600; }
  .letter--shade { color: var(--wine); z-index: 3; }
  .letter--main { color: var(--crimson); z-index: 4; mix-blend-mode: multiply; }
  .letter--script { font-style: italic; }
</style>
</head>
<body>
<main class="sheet">
  <!-- Nero D'Avola -->
  <section class="label">
    <h2 class="label__variety"><span>Nero</span><span class="indent">D'Avola</span></h2>
    <span class="letter letter--ghost" style="left:8px; top:30px; font-size:300px;">N</span>
    <div class="label__dancer" role="img" aria-label="Schwarzweißfoto einer Tänzerin mit wehendem Tuch" style="left:30px; top:110px; width:210px; height:288px;"></div>
    <span class="letter letter--shade" style="left:30px; top:90px; font-size:290px;">N</span>
    <span class="letter letter--main" style="left:24px; top:86px; font-size:290px;">N</span>
  </section>

  <!-- Cabernet Sauvignon -->
  <section class="label">
    <h2 class="label__variety"><span>Cabernet</span><span class="indent-wide">Sauvignon</span></h2>
    <span class="letter letter--ghost letter--script" style="left:40px; top:20px; font-size:320px;">C</span>
    <div class="label__dancer" role="img" aria-label="Schwarzweißfoto einer Tänzerin im Ausfallschritt mit fließendem Stoff" style="left:0; top:100px; width:252px; height:298px;"></div>
    <span class="letter letter--shade letter--script" style="left:30px; top:68px; font-size:310px;">C</span>
    <span class="letter letter--main letter--script" style="left:24px; top:64px; font-size:310px;">C</span>
  </section>

  <!-- Frappato -->
  <section class="label">
    <h2 class="label__variety"><span>Frappato</span></h2>
    <span class="letter letter--ghost" style="left:20px; top:40px; font-size:320px;">F</span>
    <div class="label__dancer" role="img" aria-label="Schwarzweißfoto einer springenden Tänzerin mit Schleier" style="left:20px; top:60px; width:232px; height:240px;"></div>
    <span class="letter letter--shade" style="left:58px; top:68px; font-size:280px;">F</span>
    <span class="letter letter--main" style="left:52px; top:64px; font-size:280px;">F</span>
  </section>
</main>
</body>
</html>
```